New Interrior Decoration company needs new website

We need a website for our new company specialising in interior decoration to residential and commercial markets.
We supply and install decorative and printed films for office and home decoration such as feature walls.
We would like to keep the design simple and clean.

Target Market(s)

Architects and interior designaers

Industry/Entity Type

It Company

Number of Pages Required

5+ page

Font styles to use
Sans Serif

Requirements
Must have
• Home page,
• Services/products page (split into commercial and residential)
• Gallery (split into commercial and residential)
• contact form and page
Nice to have
• Very clean and minimalistic design.

```html
<!DOCTYPE html>
<html lang="en">
<head>
<meta charset="utf-8">
<title>Lumen Interiors</title>
<link href="https://fonts.googleapis.com/css2?family=Roboto:wght@300;400;500;700&display=swap" rel="stylesheet">
<style>
:root{
  --page:#ececec;
  --ink:#0c0c0c;
  --blue:#1c63c4;
  --grey:#8b8b8e;
  --band:#2c2c2e;
  --footer:#1c1c1d;
  --white:#ffffff;
  --muted:#9a9a9c;
}
*{box-sizing:border-box;margin:0;padding:0}
html,body{width:1200px;height:3850px;overflow:hidden}
body{background:var(--page);font-family:"Roboto",Arial,sans-serif;color:var(--white)}
.hero{position:relative;height:610px;background:linear-gradient(180deg,#55585c 0%,#8c8f92 35%,#b9b7b2 60%,#6c6a67 100%);overflow:hidden}
.hero-nav{position:absolute;top:44px;left:96px;display:flex;gap:34px;font-size:17px;font-weight:500}
.hero-nav a{color:var(--white);text-decoration:none}
.brand{display:flex;align-items:center;gap:12px;font-weight:700;letter-spacing:1px;text-transform:uppercase}
.hero .brand{position:absolute;top:138px;left:0;right:0;justify-content:center;font-size:34px}
.brand-square{width:40px;height:40px;background:var(--white)}
.hero-title{position:absolute;top:272px;left:0;right:0;text-align:center;font-size:40px;font-weight:700}
.hero-sub{position:absolute;top:324px;left:0;right:0;text-align:center;font-size:18px;font-weight:500;letter-spacing:1.5px;text-transform:uppercase}
.quote-band{position:absolute;bottom:0;left:0;right:0;height:74px;background:rgba(20,20,20,.88);display:flex;justify-content:center;align-items:center;gap:22px}
.quote-input{width:260px;height:40px;background:var(--white);color:#777;font-size:13px;padding:12px 16px}
.quote-btn{height:40px;padding:0 18px;background:var(--blue);font-size:15px;font-weight:500;display:flex;align-items:center}
.rows{padding-top:19px}
.row{display:flex;gap:10px;margin-bottom:16px}
.panel{display:flex;flex-direction:column;justify-content:center;text-align:center;padding:0 50px}
.panel h2{font-size:22px;font-weight:700;margin-bottom:14px}
.panel p{font-size:13.5px;line-height:1.42;font-weight:400}
.panel-dark{background:var(--ink)}
.panel-blue{background:var(--blue)}
.wide{width:658px}
.narrow{width:532px}
.blue-wide{width:660px}
.photo-left{width:530px}
.filler{background:var(--grey)}
.photo{display:block}
.band-cta{height:95px;background:var(--band);display:flex;justify-content:center;align-items:center;gap:34px;margin-top:-16px}
.band-cta span{font-size:28px;font-weight:300}
.band-cta a{background:var(--blue);color:var(--white);text-decoration:none;font-size:17px;font-weight:500;padding:11px 26px}
.site-footer{position:relative;height:400px;background:var(--footer);padding:70px 96px 0}
.site-footer .brand{font-size:24px}
.site-footer .brand-square{width:30px;height:30px}
.footer-about{width:330px;margin-top:22px;font-size:13px;line-height:1.5;color:var(--muted)}
.footer-copy{margin-top:24px;font-size:12px;color:var(--muted)}
.footer-col{position:absolute;top:70px}
.footer-col h3{font-size:16px;font-weight:500;margin-bottom:14px}
.footer-col p{font-size:13px;line-height:1.6;color:var(--muted)}
.col-contact{left:690px}
.col-follow{left:925px}
.socials{display:flex;gap:12px}
.socials span{width:20px;height:20px;background:var(--muted)}
.cards{position:absolute;left:96px;bottom:40px;display:flex;gap:14px}
.cards span{width:46px;height:22px;border-radius:3px;background:#3b3b3d}
.to-top{position:absolute;right:96px;bottom:40px;display:flex;align-items:center;gap:10px;font-size:14px;color:var(--muted)}
.to-top svg{display:block}
</style>
</head>
<body>
<header class="hero">
  <svg class="photo" width="1200" height="610" style="position:absolute;inset:0" role="img" aria-label="Photo of a modern interior with dining table, chairs and pendant lights">
    <defs><linearGradient id="heroShade" x1="0" y1="0" x2="0" y2="1"><stop offset="0" stop-color="#3f4245"/><stop offset=".5" stop-color="#a9a7a2"/><stop offset="1" stop-color="#4e4d4b"/></linearGradient></defs>
    <rect width="1200" height="610" fill="url(#heroShade)" opacity=".85"/>
  </svg>
  <nav class="hero-nav"><a href="#">About</a><a href="#">Services</a><a href="#">Gallery</a><a href="#">Contact</a></nav>
  <div class="brand"><span class="brand-square"></span>Lumen Interiors</div>
  <h1 class="hero-title">Stylish, Innovative Workmanship</h1>
  <p class="hero-sub">Symbol of extraordinary space and great design</p>
  <div class="quote-band"><div class="quote-input">Enter your email here</div><div class="quote-btn">Quote Today</div></div>
</header>

<main class="rows">
  <section class="row" style="height:300px">
    <div class="panel panel-dark wide"><h2>Interior Decoration</h2><p>Lumen Interiors are involved in all aspects of the interior decoration process, from concept to completion. We work with interior designers and architects to achieve specific project requirements and we are also involved in the ideas and installation stages to help create the right interior environment for every need. The variety of looks and finishes that we offer, mixed with the varied trade and design skills we have, means that we are the right fit for all high quality interior projects. We offer specialty services in Kitchen Rejuvenation and Refurbishing, Custom Feature Walls and Decorative Films and Coverings for Interior Walls and Windows. Whatever Interior Decoration needs you have, Lumen Interiors has a solution for you.</p></div>
    <svg class="photo" width="532" height="300" role="img" aria-label="Photo of a lounge with a red feature wall and shelving"><rect width="532" height="300" fill="#6b3b33"/><rect width="532" height="300" fill="url(#g1)"/><defs><linearGradient id="g1" x1="0" x2="1"><stop offset="0" stop-color="#8a2f24" stop-opacity=".6"/><stop offset="1" stop-color="#2a2a2c" stop-opacity=".7"/></linearGradient></defs></svg>
  </section>

  <section class="row" style="height:300px">
    <svg class="photo" width="530" height="300" role="img" aria-label="Photo of a corridor with a white wall decorated with large red and grey circles"><rect width="530" height="300" fill="#d9d6d0"/></svg>
    <div class="panel panel-blue blue-wide"><h2>Decorative Films/Covering</h2><p>Enhance your decor with our extensive range of Decorative Films and Coverings. Give a melamine desk a nice hardwood finish or a glass cabinet a modern stone looking shelf. Make a wall into a bold and textured feature or screen a glass into a decorative window. Whether it is in the kitchen or the bedroom, the office or the boardroom, Lumen Interiors range of Decorative Films and Coverings meets every need. Our team of experienced installers can come on site so we can provide you with self finish or supply for other options that meet all customers' requirements. The design team can come up with artwork specific to clients' demands, or can incorporate your designs into existing environments. We can provide full art proofs so you can see what the application will look like before it is applied. Lumen Interiors' Decorative Films and Coverings are cutting edge, so look as good in a just opened office complex as they do in a rejuvenated kitchen fitout. We have the right product for every interior decoration job.</p></div>
  </section>

  <section class="row" style="height:310px">
    <div class="panel panel-dark wide"><h2>Kitchen Refurbishing/Rejuvenating</h2><p>Our kitchen building and design experience means that Lumen Interiors can meet all our customers' needs. We can create the best finish for any age kitchen, giving old kitchens life and making new kitchens feel homely. With our experience and product knowledge we have access to innovative and creative applications that make our Kitchen Refurbishing and Rejuvenating techniques perfect for both high level architects and DIY home renovators. We create personalised and stylised looks for your kitchen, without having to start from scratch. Lumen Interiors range of finishes suits all panel types and existing surfaces, so there is an application for all the kitchen environments you are looking to enhance.</p></div>
    <svg class="photo" width="532" height="310" role="img" aria-label="Photo of a bright modern kitchen with timber cabinets and a window"><rect width="532" height="310" fill="#a89a86"/></svg>
  </section>

  <section class="row" style="height:300px">
    <svg class="photo" width="530" height="300" role="img" aria-label="Photo of a teal feature wall with a circle pattern in an office"><rect width="530" height="300" fill="#4f8e97"/></svg>
    <div class="panel panel-blue blue-wide"><h2>Feature Walls</h2><p>Make your feature wall something that jumps out and says hello or something that sits serenely in the background and makes you feel comfortable and at ease. Lumen Interiors has the Feature Wall solution that will work with any space you are trying to enhance. Whether it is a high definition photo quality image, a custom design or a texture fill, a Lumen Interiors Feature Wall will achieve the look and feel you want for your room. We provide a range of digital printing techniques that can meet varied needs, such as HD quality images, artistic patterns and designs, and a kaleidoscope of colours, all in an array of textures and finishes that make every Feature Wall look good. Take your room to the next level with our Custom Printed Feature Walls with Textured Laminates.</p></div>
  </section>

  <section class="row" style="height:310px">
    <div class="panel panel-dark wide"><h2>Custom Printed Wallpaper</h2><p>At Lumen Interiors we have a custom wallpaper solution for every requirement. Whether you are trying to enhance the wall behind the computer in your office or an entire hotel, our Custom Printed Wallpaper meets all needs. We have a range of adhesive options, both permanent and removable, which means the Lumen Interiors team can do the installation for you or we can provide options for self installation or for an experienced wallpaper installer. Our design team can create the right image(s) for your Custom Wallpaper, you can bring your own designs or we can work together to collaborate on a design that works for the space you are looking to transform. Take your room to the next level with our Custom Printed Feature Walls with Textured Laminates.</p></div>
    <svg class="photo" width="532" height="310" role="img" aria-label="Photo of a colourful printed wallpaper mural in a children's room"><rect width="532" height="310" fill="#5d6f8a"/></svg>
  </section>

  <section class="row" style="height:250px">
    <div class="filler photo-left"></div>
    <div class="panel panel-blue blue-wide"><h2>Custom Printed Feature Walls With<br>Textured Laminates</h2><p>At Lumen Interiors we offer a unique range of finishes that can take your feature wall to another level. The superior range of textured finishes and custom print options we have available makes any room we enhance the decor in all the more impressive when we complete it with our specialist products. If you are looking to impress, whether it is in your office or in your home, our Custom Feature Walls are just what you are looking for.</p></div>
  </section>

  <section class="row" style="height:250px">
    <div class="panel panel-dark wide"><h2>Kids rooms</h2><p>With the interior decoration applications we use at Lumen Interiors we can make any child's bedroom into the room of their dreams. We can create an environment that is one that they will remember forever, with the fairies, warriors, cartoon characters or sports heroes of their youth, all potential aspects of their room design. Our range of print and design options means we can bring to life any bedroom idea you or your child has. With Printed Feature Walls and Custom Designed Interiors we can make any kids room into one they will cherish for life.</p></div>
    <div class="filler narrow"></div>
  </section>

  <section class="row" style="height:340px">
    <div class="filler photo-left"></div>
    <div class="panel panel-blue blue-wide"><h2>Window Treatments</h2><p>Lumen Interiors window design range means that we have a finish for every glass or window treatment you require. Whether it is for privacy film, to keep people out, or decorative film, to bring people closer, we have a glass finish for every occasion. Many of our custom wallpapers work just as well on glass, so can be used as a complete wall-to-ceiling application or in pieces and patterns on glass to provide for all decorative requirements. For privacy we have complete block out options in multiple designs and colours, as well as frosted films or light diffusers that offer varying levels of opacity, perfect for every situation. Our frosted glass film options, both in the home and office environment, can come as a flat finish, to provide complete privacy, or with cut patterns or designs, to add a personalised touch to your interior environment. If you want to make your window a design element in the space you are working with, then a Lumen Interiors Window Treatment will give you exactly this.</p></div>
  </section>

  <section class="row" style="height:238px">
    <div class="panel panel-dark wide"><h2>Wall Art</h2><p>Turn your wall into a work of art. Or make art come to life on your wall. At Lumen Interiors we can make any wall into something special and unique. We have access to a massive range of existing high quality artwork or we can do something more custom just for you. Our unique range of finishes and printing techniques means that we can achieve a Wall Art design for all types of interior decoration requirements. If you want to put your own design on your wall or you want us to come up with a design just for you, Lumen Interiors Wall Art options are going to meet your needs.</p></div>
    <div class="filler narrow"></div>
  </section>
</main>

<section class="band-cta"><span>Take a look at all what we offer you</span><a href="#">Check It Out</a></section>

<footer class="site-footer">
  <div class="brand"><span class="brand-square"></span>Lumen Interiors</div>
  <p class="footer-about">The Lumen Interiors team have over 20 years experience in the design, building, vinyl application and signage trades, giving us the ability to work through any creative or architectural needs your project may require.</p>
  <p class="footer-copy">© 2016 - Lumen Interiors All rights reserved</p>
  <div class="footer-col col-contact"><h3>Contact Us</h3><p>hello@lumeninteriors.example<br>02 5550 1234</p></div>
  <div class="footer-col col-follow"><h3>Follow Us</h3><div class="socials"><span></span><span></span><span></span><span></span></div></div>
  <div class="cards"><span></span><span></span><span></span><span></span><span></span><span></span></div>
  <div class="to-top">Top<svg width="22" height="22" viewBox="0 0 22 22"><rect width="22" height="22" fill="#3b3b3d"/><path d="M6 13l5-5 5 5" stroke="#ffffff" stroke-width="2" fill="none"/></svg></div>
</footer>
</body>
</html>
```